Veldmark Supplies Business Card

Professional business card that stand out to our potential customers. Front and back with clean modern design

Industry/Entity Type

Oil and gas

Contact Information for Business Card

Name, address, website , office phone and cell number

Requirements
Must have
• Editable files for each employee

```html
<!DOCTYPE html>
<html lang="en">
<head>
<meta charset="utf-8">
<title>Veldmark Supplies Business Card</title>
<link href="https://fonts.googleapis.com/css2?family=Montserrat:wght@400;500;700;800&display=swap" rel="stylesheet">
<style>
  :root {
    --brand-red: #ec2227;
    --brand-blue: #1fa9d6;
    --card-white: #ffffff;
    --ink: #222222;
    --stage: #2e2e2e;
  }
  * { margin: 0; padding: 0; box-sizing: border-box; }
  html, body {
    width: 1200px; height: 875px; overflow: hidden;
    background: var(--stage);
    font-family: "Montserrat", sans-serif;
  }
  .sheet {
    width: 1200px; height: 875px;
    display: flex; align-items: center; justify-content: center; gap: 40px;
  }
  .card {
    width: 540px; height: 310px;
    border-radius: 22px;
    position: relative;
    overflow: hidden;
  }
  .card--front {
    background: var(--brand-red);
    display: flex; align-items: center; justify-content: center;
  }
  .brand-lockup {
    display: flex; align-items: center; gap: 14px;
  }
  .brand-lockup__square {
    width: 26px; height: 26px;
  }
  .brand-lockup__name {
    font-weight: 800; font-size: 30px; letter-spacing: 0.5px;
    text-transform: uppercase;
  }
  .card--front .brand-lockup__square { background: var(--card-white); }
  .card--front .brand-lockup__name { color: var(--card-white); }

  .card--back {
    background: var(--card-white);
    display: flex; align-items: center;
    padding: 0 30px 0 34px;
  }
  .card--back .brand-lockup { flex-direction: column; gap: 12px; width: 210px; }
  .card--back .brand-lockup__square {
    background: var(--brand-red); border-radius: 50%; width: 30px; height: 30px;
  }
  .card--back .brand-lockup__name {
    color: var(--brand-red); font-size: 22px; text-align: center; line-height: 1.15;
  }
  .divider {
    width: 1.5px; height: 180px; background: var(--brand-red);
    margin: 0 22px 0 18px;
  }
  .contact { color: var(--ink); }
  .contact__name {
    color: var(--brand-red); font-weight: 700; font-size: 22px; line-height: 1.1;
  }
  .contact__role { font-size: 12px; font-weight: 500; margin-bottom: 12px; }
  .contact__list { list-style: none; }
  .contact__item {
    display: flex; align-items: center; gap: 8px;
    font-size: 11.5px; line-height: 1.75;
  }
  .contact__icon { width: 11px; height: 11px; flex: none; fill: var(--brand-blue); }
  .contact__address { font-size: 11.5px; line-height: 1.45; margin-top: 8px; }
</style>
</head>
<body>
<main class="sheet">
  <section class="card card--front" aria-label="Card front">
    <div class="brand-lockup">
      <span class="brand-lockup__square"></span>
      <span class="brand-lockup__name">Veldmark Supplies</span>
    </div>
  </section>

  <section class="card card--back" aria-label="Card back">
    <div class="brand-lockup">
      <span class="brand-lockup__square"></span>
      <span class="brand-lockup__name">Veldmark<br>Supplies</span>
    </div>
    <div class="divider"></div>
    <div class="contact">
      <p class="contact__name">Karim Dalton</p>
      <p class="contact__role">President</p>
      <ul class="contact__list">
        <li class="contact__item">
          <svg class="contact__icon" viewBox="0 0 12 12"><path d="M1 3c0-1 1-2 3-2h4c2 0 3 1 3 2v1H8V3H4v1H1z"/><rect x="2" y="5" width="8" height="6" rx="1"/></svg>
          +1.555.210.0400 x123
        </li>
        <li class="contact__item">
          <svg class="contact__icon" viewBox="0 0 12 12"><path d="M2 1l2-.5 1.5 3-1.2 1a7 7 0 0 0 3.2 3.2l1-1.2 3 1.5L11 10c-.3 1-1 1.5-2 1.5C4.5 11.5.5 7.5.5 3 .5 2 1 1.3 2 1z"/></svg>
          +1.555.310.2288
        </li>
        <li class="contact__item">
          <svg class="contact__icon" viewBox="0 0 12 12"><path d="M1 2.5h10v7H1z M1 2.5l5 4 5-4" stroke="#fff" stroke-width="0.8"/></svg>
          info@veldmarksupplies.com
        </li>
        <li class="contact__item">
          <svg class="contact__icon" viewBox="0 0 12 12"><circle cx="6" cy="6" r="5.5"/><path d="M.5 6h11M6 .5c-3 3-3 8 0 11M6 .5c3 3 3 8 0 11" stroke="#fff" stroke-width="0.7" fill="none"/></svg>
          www.veldmarksupplies.com
        </li>
      </ul>
      <p class="contact__address">42 Ridgeline Court<br>Calder, TX 79701 USA</p>
    </div>
  </section>
</main>
</body>
</html>
```